Brochure for people who suffer from Sleep Apnea and need a medical device called a CPAP Machine

I want a brochure that can be placed in doctors offices with my competitors brochures. It needs to be bold and stand out and deliver a very strong message that draws the patients away from our competitors and to us. I have included a word document generally outlining some of my requirements and thoughts, please review prior to investing time into design!

Target Market(s)

people who suffer from sleep apnea, which is a disease that causes them to stop breathing many times per hour, resulting in the patient needing to wear a device called a CPAP Machine. This is an illness that can impact anyone but is more likely to impact those suffering from obesity and men.

Industry/Entity Type

Health Care

Other font styles liked:
• Use what you think is best

Colors

Designer to choose colors to be used in the design.

Requirements
Must have
• Please see word document for must have items, and feel free to contact me with any questions.
• Also must have bold colors, and/or graphics to really stand out among my competitors brochures.
Nice to have
• Would prefer to use the baby picture titled "sleeping baby 4" if possible but provided 2 other baby photos just in case. Whatever you want to add, use your professional creativity! You Don't need to use all the pictures uploaded!!!!!
Should not have
• Nothing discriminatory or offensive.

```html
<!DOCTYPE html>
<html lang="en">
<head>
<meta charset="utf-8">
<title>RestWell Supply – Sleep Apnea Brochure</title>
<link href="https://fonts.googleapis.com/css2?family=Lato:wght@400;700;900&family=Roboto+Condensed:wght@700&family=Rokkitt:wght@700&family=Satisfy&display=swap" rel="stylesheet">
<style>
:root{
  --purple:#7a3a8f;
  --purple-dark:#5c2370;
  --purple-light:#a45fb8;
  --green:#3faa6a;
  --green-dark:#157a3e;
  --green-mid:#229152;
  --ink:#3b3b3b;
  --backdrop:#d4d5d7;
  --white:#ffffff;
}
*{box-sizing:border-box;margin:0;padding:0}
html,body{width:889px;height:1200px;overflow:hidden;background:var(--backdrop)}
body{font-family:'Lato',sans-serif;color:var(--ink)}
.canvas{position:relative;width:889px;height:1200px}
.spread{position:absolute;left:122px;width:655px;background:var(--white);box-shadow:0 10px 10px -6px rgba(0,0,0,.35);overflow:hidden}
.spread--outside{top:54px;height:509px}
.spread--inside{top:616px;height:508px}
.abs{position:absolute}
.photo{position:absolute}
.panel{position:absolute;top:0;height:100%}
.p1{left:0;width:214px}
.p2{left:214px;width:215px;background:linear-gradient(180deg,#2a9c5a 0%,var(--green-dark) 100%);color:var(--white);text-align:center}
.p3{left:429px;width:226px}
.intro{font-size:7.4px;line-height:1.35;color:var(--purple);text-align:justify}
.intro--green{color:var(--green-mid);text-align:left}
.feature{position:absolute;left:8px;width:200px;display:flex;gap:7px;align-items:flex-start}
.feature-icon{flex:none;width:27px;height:27px;border-radius:50%;background:var(--purple);border:2px solid #d8c3df;display:flex;align-items:center;justify-content:center}
.feature-title{font-size:6.6px;font-weight:700;color:var(--purple);text-transform:uppercase;line-height:1.1}
.feature-text{font-size:6px;line-height:1.2;color:#222}
.script{font-family:'Satisfy',cursive}
.slab{font-family:'Rokkitt',serif;font-weight:700}
.phone-pill{position:absolute;display:flex;align-items:center;justify-content:center;gap:6px;background:var(--purple-dark);color:var(--white);border-radius:12px;font-size:15px;box-shadow:0 2px 3px rgba(0,0,0,.3)}
.brand{position:absolute;display:flex;align-items:center;gap:7px;font-family:'Lato',sans-serif;font-weight:700;color:var(--green-mid);font-size:21px}
.brand-dot{width:14px;height:14px;border-radius:50%;background:var(--purple)}
.headline{font-family:'Roboto Condensed',sans-serif;font-weight:700;color:var(--purple);text-align:center;font-size:23px;line-height:1.2}
.benefit{position:absolute;left:10px;width:420px;height:50px}
.benefit-icon{position:absolute;left:0;top:0;width:46px;height:46px;border-radius:50%;background:var(--white);box-shadow:0 2px 4px rgba(0,0,0,.25);display:flex;align-items:center;justify-content:center}
.benefit-text{position:absolute;left:61px;top:0;width:350px;font-size:9.2px;line-height:1.25;color:#444}
.diff-list{list-style:none;font-size:9.3px;line-height:17px;color:var(--white)}
.diff-list li::before{content:"";display:inline-block;width:6px;height:6px;border-radius:50%;background:var(--green);margin-right:6px;vertical-align:1px}
.talk-band{position:absolute;left:0;bottom:0;width:655px;height:28px;background:var(--green);color:var(--white);font-weight:900;font-size:10.6px;letter-spacing:.3px;display:flex;align-items:center;justify-content:center}
</style>
</head>
<body>
<div class="canvas">

  <!-- OUTSIDE SPREAD -->
  <section class="spread spread--outside">
    <!-- Panel 1 -->
    <div class="panel p1">
      <div class="photo" style="left:0;top:20px;width:214px;height:165px;background:linear-gradient(135deg,#e8e4e0,#b9b2ab 60%,#f3f1ee)" role="img" aria-label="Photo of a man asleep wearing a CPAP mask"></div>
      <svg class="abs" style="left:0;top:0" width="214" height="190" viewBox="0 0 214 190">
        <path d="M0 0H214V30C150 22 60 20 0 50Z" fill="var(--purple)"/>
        <path d="M0 50C40 32 110 26 214 30V40C120 34 50 42 0 70Z" fill="var(--green)"/>
      </svg>
      <p class="intro abs" style="left:8px;top:198px;width:198px">Anyone can give you CPAP supplies. However we are committed to providing you with exceptional customer service too.</p>
      <p class="intro intro--green abs" style="left:8px;top:232px;width:200px">How do we do this?<br>By giving you services no other CPAP retailer offers, like…</p>

      <div class="feature" style="top:258px"><span class="feature-icon"><svg width="14" height="12"><path d="M1 6L7 1L13 6V11H1Z" fill="#fff"/></svg></span><div><div class="feature-title">Free Home Visits</div><div class="feature-text">We bring the store to you so we can give you as much time you need and set up all your equipment and supplies for you.</div></div></div>
      <div class="feature" style="top:296px"><span class="feature-icon"><svg width="15" height="11"><rect x="0" y="1" width="9" height="7" fill="#fff"/><path d="M9 3H12L15 6V8H9Z" fill="#fff"/><circle cx="3" cy="9" r="2" fill="#fff"/><circle cx="12" cy="9" r="2" fill="#fff"/></svg></span><div><div class="feature-title">Free Delivery</div><div class="feature-text">So you never need to come to the store (Unless you want to!).</div></div></div>
      <div class="feature" style="top:334px"><span class="feature-icon"><svg width="12" height="12"><rect x="1" y="2" width="10" height="9" fill="none" stroke="#fff" stroke-width="1.4"/><path d="M3 7L5 9L9 5" fill="none" stroke="#fff" stroke-width="1.4"/></svg></span><div><div class="feature-title" style="margin-top:5px">Night and Weekend Appointments</div><div class="feature-text">Because not everyone works 9-to-5.</div></div></div>
      <div class="feature" style="top:370px"><span class="feature-icon"><svg width="14" height="10"><circle cx="5" cy="3" r="2.6" fill="#fff"/><circle cx="10" cy="3" r="2.6" fill="#fff"/><path d="M0 10C0 6 14 6 14 10Z" fill="#fff"/></svg></span><div><div class="feature-title" style="margin-top:6px">A Dedicated Clinician</div><div class="feature-text">Because we also want to be your friend.</div></div></div>
      <div class="feature" style="top:404px"><span class="feature-icon"><svg width="12" height="12"><circle cx="6" cy="7" r="5" fill="#fff"/><rect x="4" y="0" width="4" height="3" fill="#fff"/></svg></span><div><div class="feature-title">Hardship and Financial-Assistance Programs</div><div class="feature-text">To make sure everyone gets the care they need.</div></div></div>
      <div class="feature" style="top:440px"><span class="feature-icon"><svg width="12" height="12"><rect x="0" y="5" width="3" height="7" fill="#fff"/><path d="M4 5L7 0H8V4H12V7L10 12H4Z" fill="#fff"/></svg></span><div><div class="feature-title">Promise of Guaranteed Success</div><div class="feature-text">We offer 30-day guarantees on all supplies so you know you are getting the best care possible.</div></div></div>

      <p class="abs" style="left:10px;top:479px;font-size:6.8px;color:var(--purple)">Why are YOU Settling for LESS? Let US treat you RIGHT!</p>
      <p class="abs script" style="left:10px;top:487px;font-size:13px;color:var(--green-dark)">We Make CPAP Personal!</p>
    </div>

    <!-- Panel 2 -->
    <div class="panel p2">
      <svg class="abs" style="left:0;top:0" width="215" height="50" viewBox="0 0 215 50">
        <path d="M0 0H215V36C150 30 60 28 0 40Z" fill="var(--purple)"/>
      </svg>
      <p class="abs" style="left:0;top:93px;width:215px;font-size:11.5px;line-height:1.4">Let's make sure<br>this doesn't happen to you</p>
      <div class="abs" style="left:52px;top:122px;width:110px;height:110px;border-radius:50%;background:radial-gradient(circle,#c9ccd4,#6d7380 75%);border:3px solid rgba(255,255,255,.3)" role="img" aria-label="Photo of a frustrated man in a bulky CPAP mask"></div>
      <p class="abs" style="left:0;top:236px;width:215px;font-size:11.5px">CPAP Doesn't need to be like this!</p>
      <div class="abs" style="left:78px;top:254px;width:58px;height:58px;border-radius:50%;background:radial-gradient(circle,#f5c542,#d9921d);box-shadow:0 2px 3px rgba(0,0,0,.3)" role="img" aria-label="Satisfaction guarantee seal"></div>
      <p class="abs" style="left:0;top:326px;width:215px;font-size:8.6px;line-height:1.45">We Guarantee Your CPAP Success,<br>because your Success is our Reputation.</p>
      <p class="abs" style="left:0;top:366px;width:215px;font-size:8.8px;font-weight:700;letter-spacing:-.2px">Call for an Appointment (Or just to talk) Today</p>
      <div class="phone-pill" style="left:26px;top:386px;width:162px;height:22px"><svg width="12" height="12" viewBox="0 0 12 12"><circle cx="6" cy="6" r="5.3" fill="none" stroke="#fff" stroke-width="1"/><path d="M4 3.2L5 4.6L4.5 5.3C5 6.3 5.7 7 6.7 7.5L7.4 7L8.8 8L8.2 8.9C6 9 3 6 3.1 3.8Z" fill="#fff"/></svg>555-014-2290</div>
      <p class="abs" style="left:0;top:418px;width:215px;font-size:9px;line-height:1.5">48 Harbour Lane<br>Port Mira, Ontario L0S 1A0<br>Serving all of Ontario</p>
      <p class="abs" style="left:0;top:460px;width:215px;font-size:9px;font-weight:700;letter-spacing:.8px">www.restwellsupply.com</p>
      <p class="abs script" style="left:0;top:479px;width:215px;font-size:17px">We Bring The Store To You</p>
    </div>

    <!-- Panel 3 -->
    <div class="panel p3">
      <div class="brand" style="left:32px;top:60px"><span class="brand-dot"></span>RestWell Supply</div>
      <div class="photo" style="left:0;top:118px;width:226px;height:292px;background:linear-gradient(180deg,#f2eef0 0%,#b4a3a8 40%,#8a7a78 60%,#d8cfc8 100%)" role="img" aria-label="Photo of a newborn baby sleeping peacefully"></div>
      <svg class="abs" style="left:0;top:80px" width="226" height="60" viewBox="0 0 226 60">
        <path d="M0 0C70 25 150 30 226 10V30C150 52 70 50 0 40Z" fill="var(--purple)"/>
        <path d="M0 40C70 50 150 52 226 30V34C150 58 70 58 0 46Z" fill="var(--green)"/>
        <path d="M0 46C70 58 150 58 226 34V60H0Z" fill="#f4f0f2"/>
      </svg>
      <h1 class="headline abs" style="left:0;top:141px;width:226px">WANT TO SLEEP LIKE<br>A BABY AGAIN?</h1>
      <svg class="abs" style="left:0;top:360px" width="226" height="149" viewBox="0 0 226 149">
        <path d="M0 20C80 0 160 0 226 20V149H0Z" fill="var(--purple)"/>
        <path d="M0 26C80 8 160 8 226 26V149H0Z" fill="var(--white)"/>
      </svg>
      <p class="abs slab" style="left:0;top:412px;width:226px;text-align:center;font-size:17px;color:var(--purple)">We Bring The Store To You</p>
      <p class="abs" style="left:0;top:437px;width:226px;text-align:center;font-size:11.5px;color:var(--green-mid)">Serving all of Ontario</p>
      <div class="phone-pill" style="left:31px;top:459px;width:164px;height:22px"><svg width="12" height="12" viewBox="0 0 12 12"><circle cx="6" cy="6" r="5.3" fill="none" stroke="#fff" stroke-width="1"/><path d="M4 3.2L5 4.6L4.5 5.3C5 6.3 5.7 7 6.7 7.5L7.4 7L8.8 8L8.2 8.9C6 9 3 6 3.1 3.8Z" fill="#fff"/></svg>555-014-2290</div>
      <p class="abs" style="left:0;top:488px;width:226px;text-align:center;font-size:9.5px;font-weight:700;letter-spacing:.9px;color:var(--green-mid)">www.restwellsupply.com</p>
    </div>
  </section>

  <!-- INSIDE SPREAD -->
  <section class="spread spread--inside">
    <div class="photo" style="left:0;top:0;width:429px;height:195px;background:linear-gradient(120deg,#e9e2da,#c7b8a8 45%,#f1ece6 80%)" role="img" aria-label="Photo of a smiling couple in bed, the man wearing a CPAP mask"></div>
    <svg class="abs" style="left:0;top:140px" width="655" height="90" viewBox="0 0 655 90">
      <path d="M0 30C120 90 300 60 429 40C520 25 600 30 655 42V90H0Z" fill="var(--white)"/>
      <path d="M0 25C120 72 300 48 429 32C520 22 600 24 655 36V42C600 30 520 28 429 40C300 60 120 88 0 38Z" fill="var(--green)"/>
    </svg>

    <p class="abs" style="left:13px;top:204px;width:410px;font-size:11px;line-height:1.5;color:var(--green-mid)">When you get diagnosed with Obstructive Sleep Apnea it can be overwhelming.<br>We are here to help.&nbsp; We will:</p>

    <div class="benefit" style="top:248px">
      <span class="benefit-icon"><svg width="22" height="18"><path d="M1 9L9 2L17 9V17H1Z" fill="var(--green)"/><circle cx="17" cy="12" r="4" fill="var(--purple)"/></svg></span>
      <p class="benefit-text" style="top:4px">Visit you in the comfort of your own home so we can privately discuss Sleep Apnea, explain what to expect next, and answer any and all your questions in a relaxed, comfortable environment. You don't get this from any other CPAP Retailer.</p>
    </div>
    <div class="benefit" style="top:311px">
      <span class="benefit-icon"><svg width="22" height="22"><circle cx="8" cy="13" r="5" fill="none" stroke="var(--green)" stroke-width="3" stroke-dasharray="3 2"/><circle cx="16" cy="6" r="3.5" fill="none" stroke="var(--green)" stroke-width="2.4" stroke-dasharray="2 1.5"/></svg></span>
      <p class="benefit-text" style="top:10px">Figure out the best equipment and supplies you need to guarantee your success… We will even set up everything for before we leave so you know it is set up right!</p>
    </div>
    <div class="benefit" style="top:375px">
      <span class="benefit-icon"><svg width="18" height="18"><rect x="0" y="7" width="4" height="11" fill="var(--green)"/><path d="M5 7L10 0H12V5H18V10L15 18H5Z" fill="var(--green)"/></svg></span>
      <p class="benefit-text" style="top:10px">We are committed to your success.<br>We will spend as much time with you as necessary to make sure all your questions are answered and every concern is addressed.</p>
    </div>

    <p class="abs" style="left:8px;top:448px;font-size:8.6px;color:#444">There are many resources available for you on our website at <b style="color:#333">www.<span style="color:var(--purple)">restwell</span>supply.com</b></p>

    <!-- Right panel -->
    <div class="panel p3" style="background:linear-gradient(180deg,var(--purple) 35%,var(--purple-dark) 100%)">
      <svg class="abs" style="left:0;top:0" width="226" height="190" viewBox="0 0 226 190">
        <path d="M0 0H226V168C150 152 60 170 0 190Z" fill="var(--white)"/>
      </svg>
      <div class="brand" style="left:28px;top:70px"><span class="brand-dot"></span>RestWell Supply</div>
      <p class="abs" style="left:10px;top:203px;font-size:11.5px;font-weight:700;color:var(--white)">What Makes us Different?</p>
      <ul class="diff-list abs" style="left:10px;top:226px;width:215px">
        <li>Everything!</li>
        <li>Free Home Visits</li>
        <li>Free delivery</li>
        <li>Night and weekend appointments</li>
        <li>Specializes exclusively in Sleep Therapy</li>
        <li>A dedicated clinician assigned directly to you</li>
        <li>Hardship and financial-assistance programs</li>
      </ul>
      <svg class="abs" style="left:81px;top:374px" width="64" height="14" viewBox="0 0 64 14">
        <g fill="var(--green)">
          <path id="star" d="M7 0L8.8 4.8H14L9.8 7.8L11.4 13L7 9.9L2.6 13L4.2 7.8L0 4.8H5.2Z"/>
          <use href="#star" x="12.5"/><use href="#star" x="25"/><use href="#star" x="37.5"/><use href="#star" x="50"/>
        </g>
      </svg>
      <p class="abs" style="left:0;top:400px;width:226px;text-align:center;font-size:9px;line-height:1.55;color:var(--white)">Check out our 5-Star reviews online<br>(By Searching for RestWell Supply)!</p>
      <p class="abs" style="left:0;top:444px;width:226px;display:flex;justify-content:center;align-items:center;gap:5px;font-size:10px;letter-spacing:1px;color:var(--white)">Call Us <svg width="12" height="12" viewBox="0 0 12 12"><circle cx="6" cy="6" r="5.3" fill="none" stroke="#fff" stroke-width="1"/><path d="M4 3.2L5 4.6L4.5 5.3C5 6.3 5.7 7 6.7 7.5L7.4 7L8.8 8L8.2 8.9C6 9 3 6 3.1 3.8Z" fill="#fff"/></svg> 555-014-2290</p>
    </div>

    <div class="talk-band">WE LOVE TO TALK. YOU DON'T HAVE TO BE A CUSTOMER TO CALL US, WE WILL ANSWER ANY QUESTIONS YOU HAVE!</div>
  </section>

</div>
</body>
</html>
```